BRISKEL Need a luxury modern business card designed.

Need a luxury modern business card designed. refer to the uploaded files for the company name and logo in the zip file under source files. i will making my descion on monday. so please send in before then so if we need to edit we will have the time. we have a trade show coming up and im on a deadline for printer.

Target Market(s)

high end clients

Contact Information for Business Card

Company nAme and logo. Tobias Fennick Co-Founder / Project Manager Office # 555-318-7094 Cell # 555-642-1586 BRISKEL.CA Tobias@briskel-example.ca

Font styles to use
Other font styles liked:
• Modern

Requirements
Must have
• Company name and logo, contact info, using the black, gold and white color scheme.

```html
<!DOCTYPE html>
<html lang="en">
<head>
<meta charset="utf-8">
<title>BRISKEL Business Card</title>
<link rel="stylesheet" href="https://fonts.googleapis.com/css2?family=Montserrat:wght@300;400;500;700&display=swap">
<style>
  :root {
    --charcoal: #383536;
    --gold-band: #b9a24a;
    --gold-muted: #8c8350;
    --ink: #333132;
    --paper: #ffffff;
    --rule: #4a4748;
  }
  html, body {
    margin: 0;
    padding: 0;
    width: 1200px;
    height: 1200px;
    overflow: hidden;
    background: var(--paper);
    font-family: "Montserrat", sans-serif;
  }
  .canvas {
    position: relative;
    width: 1200px;
    height: 1200px;
  }
  .card {
    position: absolute;
    left: 220px;
    width: 761px;
    height: 455px;
    box-sizing: border-box;
    box-shadow: 8px 8px 10px rgba(0, 0, 0, 0.35);
  }
  /* Front */
  .card-front {
    top: 95px;
    background: var(--charcoal);
    border-left: 6px solid var(--gold-band);
    border-bottom: 6px solid var(--gold-band);
  }
  .front-name {
    position: absolute;
    left: 0;
    right: 0;
    top: 255px;
    margin: 0;
    text-align: center;
    font-weight: 300;
    font-size: 52px;
    letter-spacing: 14px;
    color: var(--paper);
    line-height: 1;
    padding-left: 14px;
  }
  .front-web {
    position: absolute;
    left: 0;
    right: 0;
    top: 404px;
    text-align: center;
    font-weight: 400;
    font-size: 14px;
    letter-spacing: 0.5px;
    color: var(--paper);
  }
  /* Back */
  .card-back {
    top: 649px;
    background: var(--paper);
    border: 1px solid var(--rule);
  }
  .back-name {
    position: absolute;
    left: 80px;
    width: 262px;
    top: 250px;
    margin: 0;
    text-align: center;
    font-weight: 300;
    font-size: 36px;
    letter-spacing: 9px;
    color: var(--ink);
    line-height: 1;
    padding-left: 9px;
  }
  .divider {
    position: absolute;
    left: 379px;
    top: 113px;
    width: 2px;
    height: 231px;
    background: var(--rule);
  }
  .contact {
    position: absolute;
    left: 419px;
    top: 176px;
    color: var(--ink);
  }
  .contact-name {
    margin: 0;
    font-weight: 700;
    font-size: 25px;
    line-height: 1;
  }
  .contact-role {
    margin: 10px 0 14px;
    font-weight: 500;
    font-size: 16px;
    line-height: 1;
  }
  .contact-list {
    list-style: none;
    margin: 0;
    padding: 0;
  }
  .contact-list li {
    display: flex;
    align-items: center;
    height: 28px;
    font-weight: 700;
    font-size: 19px;
  }
  .contact-list svg {
    width: 20px;
    height: 20px;
    margin-right: 10px;
    flex: none;
  }
  .address {
    position: absolute;
    left: 0;
    right: 0;
    top: 383px;
    text-align: center;
    font-weight: 400;
    font-size: 15px;
    color: var(--ink);
  }
</style>
</head>
<body>
<main class="canvas">
  <section class="card card-front" aria-label="Card front">
    <h1 class="front-name">BRISKEL</h1>
    <p class="front-web">WWW.BRISKEL.CA</p>
  </section>

  <section class="card card-back" aria-label="Card back">
    <h2 class="back-name">BRISKEL</h2>
    <div class="divider"></div>
    <div class="contact">
      <h3 class="contact-name">Tobias Fennick</h3>
      <p class="contact-role">Project Manager</p>
      <ul class="contact-list">
        <li>
          <svg viewBox="0 0 20 20" aria-hidden="true">
            <rect x="5" y="1.5" width="10" height="17" rx="2" fill="none" stroke="var(--gold-muted)" stroke-width="2"/>
            <circle cx="10" cy="15" r="1.1" fill="var(--gold-muted)"/>
          </svg>
          555-642-1586
        </li>
        <li>
          <svg viewBox="0 0 20 20" aria-hidden="true">
            <path d="M5 2 L8 2 L9.5 6 L7.5 8 C8.5 10.5 10 12 12.5 13 L14.5 11 L18 12.5 L18 15.5 C18 17 17 18 15.5 18 C9 17.5 2.5 11 2 4.5 C2 3 3.2 2 5 2 Z" fill="var(--gold-muted)"/>
          </svg>
          555-318-7094
        </li>
        <li>
          <svg viewBox="0 0 20 20" aria-hidden="true">
            <rect x="1.5" y="4.5" width="17" height="11" fill="none" stroke="var(--gold-muted)" stroke-width="1.6"/>
            <path d="M1.5 4.5 L10 11 L18.5 4.5 M1.5 15.5 L8 9.5 M18.5 15.5 L12 9.5" fill="none" stroke="var(--gold-muted)" stroke-width="1.6"/>
          </svg>
          Tobias@briskel-example.ca
        </li>
      </ul>
    </div>
    <p class="address">48 Marlow Crescent Unit 5, Ashford, ON L9Z 2K7</p>
  </section>
</main>
</body>
</html>
```